Lindqvar Foundation Letterhead

We are a newly established non profit registered in Maryland but operates in Africa, south of the sahara. We offer scholarships to deserving young adults from high school through college. Our color theme for our existing logo is purple, we want a design that is stylish, spellbinding yet a letterhead that projects seriousness. More information on www.thelindqvarfoundation.example

Target Market(s)

High school and college students in sub saharan African as well as our donors in the US

Industry/Entity Type

Non Profit

Font styles to use
Script

Requirements
Must have
• Logo at the top and if possible watermark the logo in the middle of the letterhead, contact address,
Should not have
• NA

```html
<!DOCTYPE html>
<html lang="en">
<head>
<meta charset="utf-8">
<title>Lindqvar Foundation Letterhead</title>
<link rel="stylesheet" href="https://fonts.googleapis.com/css2?family=Cinzel:wght@400;500&family=Didact+Gothic&display=swap">
<style>
  :root {
    --backdrop: #d6d5d8;
    --paper: #f5f5f5;
    --purple: #6a2c91;
    --purple-light: #a79fd1;
    --rule: #b9b6bd;
    --ink: #4a4a4a;
    --edge-grey: #c4c4c4;
  }
  * { margin: 0; padding: 0; box-sizing: border-box; }
  html, body { width: 1200px; height: 991px; overflow: hidden; background: var(--backdrop); }
  .letterhead {
    position: absolute; left: 270px; top: 30px; width: 661px; height: 931px;
    background: var(--paper);
  }
  .edge-accents { position: absolute; left: 0; top: 0; }
  .header {
    position: absolute; top: 62px; left: 0; width: 100%;
    display: flex; align-items: center; justify-content: center; gap: 14px;
  }
  .header-mark {
    width: 44px; height: 44px; flex: none;
    border: 3px solid var(--purple); border-radius: 50%;
  }
  .header-text { text-align: left; }
  .header-name {
    font-family: "Cinzel", serif; font-size: 17px; color: var(--purple);
    letter-spacing: 0.5px; line-height: 1.2;
  }
  .header-tagline {
    font-family: "Didact Gothic", sans-serif; font-size: 7px; letter-spacing: 1.4px;
    color: var(--purple-light); text-transform: uppercase; margin-top: 4px;
  }
  .footer { position: absolute; left: 152px; width: 356px; top: 848px; text-align: center; }
  .footer-name {
    font-family: "Cinzel", serif; font-size: 15px; color: var(--purple); letter-spacing: 0.5px;
    padding-bottom: 6px; border-bottom: 1px solid var(--rule);
  }
  .footer-contact {
    font-family: "Didact Gothic", sans-serif; font-size: 8.6px; color: var(--ink);
    line-height: 11.5px; white-space: nowrap;
  }
  .footer-contact:first-of-type { margin-top: 5px; }
  .footer-contact .label, .footer-contact .domain { color: var(--purple); font-weight: bold; }
</style>
</head>
<body>
<main class="letterhead">
  <svg class="edge-accents" width="661" height="931" viewBox="0 0 661 931" aria-hidden="true">
    <defs>
      <linearGradient id="edgePurple" x1="0" y1="0" x2="0" y2="1">
        <stop offset="0" stop-color="#6a2c91"/>
        <stop offset="0.75" stop-color="#a79fd1"/>
        <stop offset="1" stop-color="#6a2c91"/>
      </linearGradient>
    </defs>
    <path d="M0 224 Q12 467 0 710 Z" fill="url(#edgePurple)"/>
    <path d="M661 248 Q648 480 661 725 Z" fill="var(--edge-grey)"/>
  </svg>

  <header class="header">
    <div class="header-mark"></div>
    <div class="header-text">
      <p class="header-name">The Lindqvar Foundation Inc</p>
      <p class="header-tagline">Opening doors to learning for young minds</p>
    </div>
  </header>

  <footer class="footer">
    <p class="footer-name">The Lindqvar Foundation</p>
    <p class="footer-contact">240 Harbour Lane - Unit 12, Toronto, ON Canada, M5A 2K7 · <span class="label">Tel:</span> (555) 014-2287</p>
    <p class="footer-contact"><span class="label">Email:</span> info@thelindqvarfoundation.example · www.<span class="domain">thelindqvarfoundation</span>.example</p>
  </footer>
</main>
</body>
</html>
```